Core Investment Strategy's Super Pie Chart

We need a one page visual explanation of an investment strategy we call "Keystone/Orbit". This strategy emphasizes a "core" portfolio that will seldom change and "perimeter" investments that will change. Our investment management firm caters to wealthy individuals. We want to project an image of strength and reliability. At the same time, we are willing to explore new concepts. I have uploaded a PDF of my graphically-challenged assistant's attempt at creating the one page visual.

```html
<!DOCTYPE html>
<html lang="en">
<head>
<meta charset="utf-8">
<title>Keystone Orbit Portfolio</title>
<link rel="stylesheet" href="https://fonts.googleapis.com/css2?family=Cinzel:wght@400;500&display=swap">
<style>
  :root {
    --page: #ffffff;
    --panel-light: #f1f1f1;
    --panel-mid: #dedede;
    --panel-dark: #cfcfcf;
    --ink: #2b2b2b;
    --ink-soft: #3d3d3d;
    --rule: #b4b4b4;
    --green: #3aa935;
    --green-light: #8dc63f;
    --green-deep: #1e7d32;
    --green-line: #17692f;
    --slate: #555557;
    --slate-deep: #2b2b2b;
    --blue: #29a8e0;
    --blue-deep: #0f6fb6;
    --orange: #fbad3f;
    --orange-deep: #f7901e;
    --tan: #c49a6c;
    --tan-deep: #5a4636;
    --white-ring: #ffffff;
    --white-deep: #6d6e71;
    --legend-brown: #7a5430;
  }
  * { margin: 0; padding: 0; box-sizing: border-box; }
  html, body { width: 1200px; height: 900px; overflow: hidden; background: var(--page); }
  body { position: relative; font-family: "Cinzel", serif; }

  .panel {
    position: absolute; left: 37px; top: 167px; width: 1125px; height: 646px;
    background:
      radial-gradient(ellipse at 60% 40%, var(--panel-light) 0%, var(--panel-mid) 60%, var(--panel-dark) 100%);
  }
  .chart { position: absolute; left: 0; top: 0; width: 1200px; height: 900px; }

  .title {
    position: absolute; left: 585px; top: 273px;
    font-size: 40px; font-weight: 400; line-height: 1; letter-spacing: 1px;
    color: var(--ink); white-space: nowrap;
  }
  .group { position: absolute; left: 658px; list-style: none; }
  .group li {
    position: relative; height: 38px; padding-left: 60px;
    font-size: 33px; line-height: 38px; letter-spacing: 0.5px; white-space: nowrap;
  }
  .group li::before {
    content: ""; position: absolute; left: 0; top: 6px; width: 45px; height: 27px;
    clip-path: polygon(0 0, 67% 0, 100% 50%, 67% 100%, 0 100%, 31% 50%);
  }
  .equities { top: 333px; color: var(--green); }
  .equities li::before { background: linear-gradient(90deg, var(--green-light), var(--green)); }
  .bonds { top: 532px; color: var(--ink-soft); }
  .bonds li::before { background: linear-gradient(90deg, #666, #3a3a3a); }

  .divider {
    position: absolute; left: 610px; top: 512px; width: 530px; height: 3px;
    background: var(--rule);
  }

  .legend-item { position: absolute; display: flex; align-items: center; gap: 9px; line-height: 1.25; }
  .legend-dot { width: 32px; height: 32px; border-radius: 50%; flex: none; }
  .legend-others { left: 662px; top: 625px; color: var(--blue); font-size: 18px; }
  .legend-others .legend-dot { background: var(--blue); }
  .legend-alternative { left: 662px; top: 662px; color: var(--orange-deep); font-size: 13px; }
  .legend-alternative .legend-dot { background: var(--orange-deep); }
  .legend-managed { left: 809px; top: 625px; color: var(--legend-brown); font-size: 13px; }
  .legend-managed .legend-dot { background: var(--tan); }
  .legend-core { left: 809px; top: 666px; color: var(--ink); font-size: 13px; }
  .legend-core .legend-dot { background: var(--white-ring); border: 2px solid #333; }
</style>
</head>
<body>
  <div class="panel"></div>

  <svg class="chart" viewBox="0 0 1200 900" aria-hidden="true">
    <!-- header rule with marker -->
    <line x1="112" y1="244" x2="960" y2="244" stroke="var(--ink)" stroke-width="4"/>
    <rect x="81" y="230" width="28" height="28" transform="rotate(45 95 244)" fill="#f4f4f4" stroke="var(--ink)" stroke-width="3"/>
    <circle cx="95" cy="244" r="7" fill="var(--blue)"/>

    <!-- outer ring: extrusion -->
    <g fill="none" stroke-width="22" transform="translate(0 10)">
      <path d="M86.02 509.55 A247 247 0 0 1 329.55 266.02" stroke="var(--blue-deep)"/>
      <path d="M336.45 266.02 A247 247 0 0 1 579.98 509.55" stroke="var(--orange-deep)"/>
      <path d="M579.98 516.45 A247 247 0 0 1 336.45 759.98" stroke="var(--tan-deep)"/>
      <path d="M329.55 759.98 A247 247 0 0 1 86.02 516.45" stroke="var(--white-deep)"/>
    </g>
    <!-- outer ring: face -->
    <g fill="none" stroke-width="22">
      <path d="M86.02 509.55 A247 247 0 0 1 329.55 266.02" stroke="var(--blue)"/>
      <path d="M336.45 266.02 A247 247 0 0 1 579.98 509.55" stroke="var(--orange)"/>
      <path d="M579.98 516.45 A247 247 0 0 1 336.45 759.98" stroke="var(--tan)"/>
      <path d="M329.55 759.98 A247 247 0 0 1 86.02 516.45" stroke="var(--white-ring)"/>
    </g>

    <!-- inner pie: extrusion -->
    <g transform="translate(0 12)">
      <path d="M331 348 A165 165 0 0 1 447.67 629.67 L347.97 529.97 A24 24 0 0 0 331 489 Z" fill="var(--green-deep)"/>
      <path d="M447.67 629.67 A165 165 0 0 1 400.73 662.54 L341.14 534.75 A24 24 0 0 0 347.97 529.97 Z" fill="var(--green-deep)"/>
      <path d="M400.73 662.54 A165 165 0 0 1 356.81 675.97 L334.75 536.70 A24 24 0 0 0 341.14 534.75 Z" fill="var(--green-deep)"/>
      <path d="M356.81 675.97 A165 165 0 0 1 263.89 663.73 L321.24 534.92 A24 24 0 0 0 334.75 536.70 Z" fill="var(--green-deep)"/>
      <path d="M263.89 663.73 A165 165 0 0 1 214.33 396.33 L314.03 496.03 A24 24 0 0 0 321.24 534.92 Z" fill="var(--slate-deep)"/>
      <path d="M214.33 396.33 A165 165 0 0 1 331 348 L331 489 A24 24 0 0 0 314.03 496.03 Z" fill="var(--slate-deep)"/>
    </g>
    <!-- inner pie: face -->
    <g stroke-linejoin="round">
      <path d="M331 348 A165 165 0 0 1 447.67 629.67 L347.97 529.97 A24 24 0 0 0 331 489 Z" fill="var(--green-light)" stroke="var(--green-line)" stroke-width="3"/>
      <path d="M447.67 629.67 A165 165 0 0 1 400.73 662.54 L341.14 534.75 A24 24 0 0 0 347.97 529.97 Z" fill="var(--green-light)" stroke="var(--green-line)" stroke-width="3"/>
      <path d="M400.73 662.54 A165 165 0 0 1 356.81 675.97 L334.75 536.70 A24 24 0 0 0 341.14 534.75 Z" fill="var(--green-light)" stroke="var(--green-line)" stroke-width="3"/>
      <path d="M356.81 675.97 A165 165 0 0 1 263.89 663.73 L321.24 534.92 A24 24 0 0 0 334.75 536.70 Z" fill="var(--green-light)" stroke="var(--green-line)" stroke-width="3"/>
      <path d="M263.89 663.73 A165 165 0 0 1 214.33 396.33 L314.03 496.03 A24 24 0 0 0 321.24 534.92 Z" fill="var(--slate)" stroke="#000" stroke-width="2"/>
      <path d="M214.33 396.33 A165 165 0 0 1 331 348 L331 489 A24 24 0 0 0 314.03 496.03 Z" fill="var(--slate)" stroke="#000" stroke-width="2"/>
    </g>
  </svg>

  <h1 class="title">Keystone Orbit Portfolio</h1>

  <ul class="group equities">
    <li>Lg. Cap Equities</li>
    <li>Mid Cap Equities</li>
    <li>Sm. Cap Equities</li>
    <li>Int’l/dev. Cap Equities</li>
  </ul>

  <div class="divider"></div>

  <ul class="group bonds">
    <li>Intermediate Bonds</li>
    <li>Short Term Bonds</li>
  </ul>

  <div class="legend-item legend-others"><span class="legend-dot"></span><span>Others : 2%</span></div>
  <div class="legend-item legend-alternative"><span class="legend-dot"></span><span>Alternative<br>Assets : 7%</span></div>
  <div class="legend-item legend-managed"><span class="legend-dot"></span><span>Actively Managed<br>Mutual Funds, 8%</span></div>
  <div class="legend-item legend-core"><span class="legend-dot"></span><span>Attractive Core<br>Assets, 3%</span></div>
</body>
</html>
```